Government Contracting business needs a website design.

Pellworth & Quine, LLC is a minority owned Service Disabled Veteran Owned Small Business (SDVOSB) that provides Strategic Planning, Public Health Emergency Response, and Data Management Solutions for Federal Civilian and Defense Agencies. We have over 20 years of experience helping health and defense agencies develop concept of operations, deploy assets and personnel in Hot Zones around the world, and deliver goods and services all of the globe.

We are a leader in the field of Data Management. We help our customers develop cloud migration and disaster recovery strategies. We are experts with database management, data replication, queries, consolidation, and records management.

We are looking for a very nice and simple website designs that states clearly what we do as a company and that is easy for our customers to follow. We would like to have some moving pictures that are base on our expertise. We want the website to be easy to use and have the scroll down features that keeps things all on the same page when clicking on the menu. I attached a document with what we need on the website. I will also attach our logo. We want it to look simple clean and very professional.

Target Market(s)

Government Contracting, Management Consulting, Health

Industry/Entity Type

Government

Coding

Coded - Design and coding required

Number of Pages Required

1 page

Font styles to use
Serif

Requirements
Must have
• Very nice picture slides that speaks to our capabilities in Disaster Response, Strategic Planning, and Database Management. Slick look and design. Make sure SDVOSB Logo is right at the beginning of website as our customers is looking for that certification. Very nice colors that blend well with our logo.
Nice to have
• Very nice and slick colors that blends well with logo.
Should not have
• Basic website design that are weary on the eye. No bright colors, just simple colors that looks good with logo.

```html
<!DOCTYPE html>
<html lang="en">
<head>
<meta charset="utf-8">
<title>Pellworth &amp; Quine, LLC</title>
<link href="https://fonts.googleapis.com/css2?family=Montserrat:wght@500;600;700&family=Open+Sans:wght@400;600;700&display=swap" rel="stylesheet">
<style>
:root{
  --navy:#2b4a5d;
  --navy-deep:#1d3345;
  --ink:#2a2a2a;
  --body:#555b61;
  --icon:#5a5f64;
  --rule:#cfd3d6;
  --accent:#3ea0dc;
  --footer:#28292b;
  --footer-text:#d8d8d8;
  --white:#ffffff;
}
*{margin:0;padding:0;box-sizing:border-box}
html,body{width:1200px;height:3502px;overflow:hidden;background:var(--white)}
body{position:relative;font-family:"Open Sans",Arial,sans-serif;color:var(--body)}
.abs{position:absolute}
h1,h2,h3,.brand-name,.btn,.nav a{font-family:"Montserrat",Arial,sans-serif}

/* hero */
.hero{position:absolute;left:0;top:0;width:1200px;height:660px;overflow:hidden}
.hero-photo{position:absolute;inset:0;background:linear-gradient(125deg,#1c2c44 0%,#2e3f5c 40%,#4a5468 60%,#1e2b40 100%)}
.hero-wave{position:absolute;left:0;bottom:0}
.brand{position:absolute;display:flex;align-items:center;gap:12px}
.brand-mark{width:26px;height:26px;background:var(--white)}
.brand-name{color:var(--white);font-weight:600;font-size:25px;letter-spacing:.3px}
.brand-sub{display:block;font-family:"Open Sans",Arial,sans-serif;font-size:10px;font-weight:400;letter-spacing:.5px;margin-top:2px}
.nav{position:absolute;left:552px;top:62px;display:flex;gap:30px}
.nav a{color:var(--white);text-decoration:none;font-size:14px;font-weight:600;letter-spacing:.3px}
.nav a.active{color:var(--accent)}
.nav-search{position:absolute;left:1088px;top:63px}
.hero-title{position:absolute;left:0;top:215px;width:1200px;text-align:center;color:var(--white);font-size:42px;font-weight:700;line-height:62px;letter-spacing:.5px}
.btn{position:absolute;display:flex;align-items:center;justify-content:center;border-radius:30px;font-size:15px;font-weight:600;text-transform:uppercase;letter-spacing:.3px}
.btn-light{border:2px solid var(--white);color:var(--white)}
.btn-dark{border:2px solid var(--navy);color:var(--navy)}
.dots{position:absolute;left:562px;top:533px;display:flex;gap:5px}
.dots span{width:12px;height:12px;border-radius:50%;border:2px solid var(--white)}
.dots span.on{background:var(--white)}

/* welcome */
.cert-badge{position:absolute;left:100px;top:728px;width:246px;height:230px}
.v-rule{position:absolute;left:405px;top:755px;width:2px;height:180px;background:var(--rule)}
.section-title{color:var(--navy);font-size:33px;font-weight:600;letter-spacing:.3px}
.welcome-title{position:absolute;left:470px;top:724px}
.welcome-text{position:absolute;left:470px;top:785px;width:635px;font-size:15px;line-height:29px}
.h-rule{position:absolute;left:98px;width:1004px;height:2px;background:var(--rule)}
.center-title{position:absolute;left:0;width:1200px;text-align:center}

/* capabilities */
.cap{position:absolute;top:1240px;width:360px;text-align:center}
.cap svg{display:block;margin:0 auto}
.cap h3{margin-top:42px;color:var(--ink);font-size:21px;font-weight:600}
.cap p{margin-top:16px;font-size:15px;line-height:26px}

/* why hire */
.why{position:absolute;left:0;top:1610px;width:1200px;height:500px}
.why-panel{position:absolute;left:0;top:0;width:596px;height:500px;background:var(--navy)}
.why-photo{position:absolute;left:596px;top:0;width:604px;height:500px;background:linear-gradient(135deg,#8d8e8f 0%,#b9b6b2 45%,#8b857e 75%,#4d5a45 100%)}
.why h2{position:absolute;left:98px;top:58px;color:var(--white);font-size:33px;font-weight:600}
.why ul{position:absolute;left:98px;top:124px;width:450px;list-style:none}
.why li{position:relative;padding-left:27px;color:var(--white);font-size:15px;line-height:28px;margin-bottom:27px}
.why li svg{position:absolute;left:0;top:6px}

/* blog */
.post{position:absolute;top:2270px;width:324px}
.post-img{width:324px;height:185px}
.post h3{margin-top:40px;color:var(--ink);font-size:20px;font-weight:600}
.post-meta{margin-top:12px;font-size:13px;display:flex;align-items:center;gap:7px}
.post p{margin-top:12px;font-size:15px;line-height:24px}
.read-more{display:block;margin-top:18px;color:var(--navy-deep);font-family:"Montserrat",Arial,sans-serif;font-weight:700;font-size:14px}

/* partners */
.partner{position:absolute;top:2850px;width:237px;height:98px;border:1px solid #bfc3c6;display:flex;align-items:center;justify-content:center;color:var(--ink);font-family:"Montserrat",Arial,sans-serif;font-size:21px;font-weight:700}

/* footer */
.footer{position:absolute;left:0;top:3020px;width:1200px;height:482px}
.footer-base{position:absolute;left:0;top:0}
.footer-col{position:absolute;top:190px;color:var(--footer-text)}
.footer-col h3{color:var(--white);font-size:19px;font-weight:500}
.footer-links{list-style:none;margin-top:22px}
.footer-links li{font-size:13px;line-height:25px}
.footer-col p{font-size:13px;line-height:23px}
.email-field{margin-top:16px;width:255px;height:36px;border:1px solid #aaa;font-size:13px;padding:8px 12px;color:var(--white)}
.subscribe{margin-top:16px;width:100px;height:34px;border:2px solid var(--white);border-radius:20px;color:var(--white);font-size:12px;font-weight:700;display:flex;align-items:center;justify-content:center;font-family:"Montserrat",Arial,sans-serif}
.contact-row{position:relative;padding-left:34px;margin-bottom:20px;font-size:13px;line-height:22px}
.contact-row svg{position:absolute;left:0;top:3px}
.footer-rule{position:absolute;left:98px;top:392px;width:1004px;height:1px;background:#444}
.copyright{position:absolute;left:98px;top:427px;font-size:13px;color:var(--footer-text)}
.socials{position:absolute;left:990px;top:420px;display:flex;gap:11px}
.socials span{width:32px;height:32px;border-radius:50%;border:2px solid var(--footer-text)}
</style>
</head>
<body>

<header class="hero">
  <div class="hero-photo" role="img" aria-label="Photo of people reviewing charts on a laptop at a desk"></div>
  <svg class="hero-wave" width="1200" height="150" viewBox="0 0 1200 150"><path d="M0 120 C200 130 380 30 620 40 C820 48 950 95 1200 70 L1200 150 L0 150 Z" fill="#ffffff"/></svg>
  <div class="brand" style="left:100px;top:44px">
    <span class="brand-mark"></span>
    <span class="brand-name">Pellworth &amp; Quine<span class="brand-sub">A Health IT Company</span></span>
  </div>
  <nav class="nav">
    <a class="active">HOME</a><a>ABOUT</a><a>SERVICES</a><a>CAPABILITIES</a><a>JOB</a><a>CONTACT</a>
  </nav>
  <svg class="nav-search" width="16" height="16" viewBox="0 0 16 16"><circle cx="6.5" cy="6.5" r="4.8" fill="none" stroke="#fff" stroke-width="2.2"/><line x1="10" y1="10" x2="14.5" y2="14.5" stroke="#fff" stroke-width="2.4" stroke-linecap="round"/></svg>
  <h1 class="hero-title">A HEALTH IT AND ACQUISITION FOR THE<br>DEFENSE AND VA COMMUNITY</h1>
  <a class="btn btn-light" style="left:422px;top:365px;width:168px;height:56px">Join Us!</a>
  <a class="btn btn-light" style="left:610px;top:365px;width:168px;height:56px">Explore More</a>
  <div class="dots"><span class="on"></span><span></span><span></span><span></span></div>
</header>

<section class="welcome">
  <svg class="cert-badge" viewBox="0 0 246 230" role="img" aria-label="SDVOSB certification badge">
    <circle cx="123" cy="113" r="108" fill="#ffffff" stroke="#1f3f8f" stroke-width="14"/>
    <circle cx="123" cy="113" r="72" fill="none" stroke="#c0282d" stroke-width="6"/>
    <rect x="58" y="96" width="130" height="36" fill="#c0282d"/>
  </svg>
  <div class="v-rule"></div>
  <h2 class="section-title welcome-title">WELCOME TO PELLWORTH &amp; QUINE</h2>
  <p class="welcome-text">Pellworth &amp; Quine, LLC is a minority owned Service Disabled Veteran Owned Small Business (SDVOSB) that provides Strategic Planning, Public Health Emergency Response, and Data Management Solutions for Federal Civilian and Defense Agencies. We have over 20 years of experience helping health and defense agencies develop concept of operations, deploy assets and personnel in Hot Zones around the world, and deliver goods and services all of the globe.</p>
  <a class="btn btn-dark" style="left:470px;top:965px;width:150px;height:56px">About Us</a>
</section>

<div class="h-rule" style="top:1097px"></div>

<section class="capabilities">
  <h2 class="section-title center-title" style="top:1162px">CORE CAPABILITIES</h2>
  <div class="cap" style="left:60px">
    <svg width="110" height="120" viewBox="0 0 110 120">
      <g stroke="#5a5f64" stroke-width="5" stroke-linecap="round">
        <line x1="55" y1="4" x2="55" y2="14"/><line x1="18" y1="20" x2="25" y2="27"/><line x1="92" y1="20" x2="85" y2="27"/><line x1="4" y1="55" x2="14" y2="55"/><line x1="96" y1="55" x2="106" y2="55"/>
      </g>
      <path d="M55 24 a32 32 0 0 1 20 57 v10 h-40 v-10 a32 32 0 0 1 20 -57 z" fill="#5a5f64"/>
      <circle cx="55" cy="56" r="12" fill="#fff"/><circle cx="55" cy="56" r="5" fill="#5a5f64"/>
      <rect x="37" y="96" width="36" height="7" rx="3" fill="#5a5f64"/><rect x="41" y="107" width="28" height="7" rx="3" fill="#5a5f64"/>
      <circle cx="96" cy="104" r="5" fill="#4aa54a"/>
    </svg>
    <h3>Strategic Planning</h3>
    <p>We are experts with database management,<br>data replication, queries, consolidation, and<br>records management.</p>
  </div>
  <div class="cap" style="left:420px">
    <svg width="110" height="120" viewBox="0 0 110 120">
      <circle cx="55" cy="60" r="46" fill="none" stroke="#5a5f64" stroke-width="14" stroke-dasharray="12 8"/>
      <circle cx="55" cy="60" r="40" fill="#5a5f64"/>
      <circle cx="55" cy="60" r="26" fill="none" stroke="#fff" stroke-width="5"/>
      <line x1="55" y1="60" x2="55" y2="42" stroke="#fff" stroke-width="5" stroke-linecap="round"/>
      <line x1="55" y1="60" x2="68" y2="60" stroke="#fff" stroke-width="5" stroke-linecap="round"/>
    </svg>
    <h3>Public Health Emergency Response</h3>
    <p>We are experts with database management,<br>data replication, queries, consolidation, and<br>records management.</p>
  </div>
  <div class="cap" style="left:780px">
    <svg width="110" height="120" viewBox="0 0 110 120">
      <g fill="#5a5f64">
        <ellipse cx="45" cy="20" rx="36" ry="11"/>
        <path d="M9 30 q36 20 72 0 v16 q-36 20 -72 0z"/>
        <path d="M9 54 q36 20 72 0 v16 q-36 20 -72 0z"/>
        <path d="M9 78 q36 20 72 0 v16 q-36 20 -72 0z"/>
      </g>
      <circle cx="80" cy="90" r="26" fill="#fff"/>
      <circle cx="80" cy="90" r="19" fill="none" stroke="#5a5f64" stroke-width="9" stroke-dasharray="7 5"/>
      <circle cx="80" cy="90" r="15" fill="#5a5f64"/><circle cx="80" cy="90" r="6" fill="#fff"/>
    </svg>
    <h3>Data Management</h3>
    <p>We are experts with database management,<br>data replication, queries, consolidation, and<br>records management.</p>
  </div>
</section>

<section class="why">
  <div class="why-panel"></div>
  <div class="why-photo" role="img" aria-label="Photo of a team pointing at charts and notes on a table"></div>
  <h2>WHY HIRE US?</h2>
  <ul>
    <li><svg width="15" height="15" viewBox="0 0 15 15"><circle cx="7.5" cy="7.5" r="7.5" fill="#fff"/><path d="M4 7.8l2.4 2.3 4.6-4.8" fill="none" stroke="#2b4a5d" stroke-width="2"/></svg>Over 20 years of experience deploying assets and personnel to disaster zones around the US and the world.</li>
    <li><svg width="15" height="15" viewBox="0 0 15 15"><circle cx="7.5" cy="7.5" r="7.5" fill="#fff"/><path d="M4 7.8l2.4 2.3 4.6-4.8" fill="none" stroke="#2b4a5d" stroke-width="2"/></svg>Over 20 years of experience developing concept of operations and stakeholder management strategies for Federal Agencies.</li>
    <li><svg width="15" height="15" viewBox="0 0 15 15"><circle cx="7.5" cy="7.5" r="7.5" fill="#fff"/><path d="M4 7.8l2.4 2.3 4.6-4.8" fill="none" stroke="#2b4a5d" stroke-width="2"/></svg>Over 10 years of experience with database management and replications</li>
    <li><svg width="15" height="15" viewBox="0 0 15 15"><circle cx="7.5" cy="7.5" r="7.5" fill="#fff"/><path d="M4 7.8l2.4 2.3 4.6-4.8" fill="none" stroke="#2b4a5d" stroke-width="2"/></svg>Highly educated consultants with over 90% possessing advance degrees and industry certifications</li>
  </ul>
</section>

<section class="blog">
  <h2 class="section-title center-title" style="top:2190px">LATEST BLOG</h2>
  <article class="post" style="left:98px">
    <div class="post-img" role="img" aria-label="Photo of a business desk with shopping bags and a laptop" style="background:linear-gradient(135deg,#c8c6c2,#8d8a86 60%,#5e5c5a)"></div>
    <h3>Finibus Bonorumet Maloru</h3>
    <div class="post-meta"><svg width="12" height="12" viewBox="0 0 12 12"><rect x="1" y="2" width="10" height="9" fill="none" stroke="#555" stroke-width="1.5"/><line x1="1" y1="5" x2="11" y2="5" stroke="#555" stroke-width="1.5"/></svg>25/09/2017 &nbsp;| &nbsp;<svg width="11" height="12" viewBox="0 0 11 12"><circle cx="5.5" cy="3.5" r="3" fill="#555"/><path d="M0 12a5.5 5 0 0 1 11 0z" fill="#555"/></svg>Ellis</div>
    <p>Neque porro quisquam est, qui dolorem ipsu ia dolor sit amet, consectetur, adipisci.</p>
    <a class="read-more">READ MORE</a>
  </article>
  <article class="post" style="left:438px">
    <div class="post-img" role="img" aria-label="Photo of a technician in a server room" style="background:linear-gradient(135deg,#0e1a2e,#1f3b5e 55%,#0b1424)"></div>
    <h3>Finibus Bonorumet Maloru</h3>
    <div class="post-meta"><svg width="12" height="12" viewBox="0 0 12 12"><rect x="1" y="2" width="10" height="9" fill="none" stroke="#555" stroke-width="1.5"/><line x1="1" y1="5" x2="11" y2="5" stroke="#555" stroke-width="1.5"/></svg>25/09/2017 &nbsp;| &nbsp;<svg width="11" height="12" viewBox="0 0 11 12"><circle cx="5.5" cy="3.5" r="3" fill="#555"/><path d="M0 12a5.5 5 0 0 1 11 0z" fill="#555"/></svg>Ellis</div>
    <p>Neque porro quisquam est, qui dolorem ipsu ia dolor sit amet, consectetur, adipisci.</p>
    <a class="read-more">READ MORE</a>
  </article>
  <article class="post" style="left:778px">
    <div class="post-img" role="img" aria-label="Photo of papers, notes and a laptop on a wooden desk" style="background:linear-gradient(135deg,#7a5b44,#a4876c 50%,#5d4434)"></div>
    <h3>Finibus Bonorumet Maloru</h3>
    <div class="post-meta"><svg width="12" height="12" viewBox="0 0 12 12"><rect x="1" y="2" width="10" height="9" fill="none" stroke="#555" stroke-width="1.5"/><line x1="1" y1="5" x2="11" y2="5" stroke="#555" stroke-width="1.5"/></svg>25/09/2017 &nbsp;| &nbsp;<svg width="11" height="12" viewBox="0 0 11 12"><circle cx="5.5" cy="3.5" r="3" fill="#555"/><path d="M0 12a5.5 5 0 0 1 11 0z" fill="#555"/></svg>Ellis</div>
    <p>Neque porro quisquam est, qui dolorem ipsu ia dolor sit amet, consectetur, adipisci.</p>
    <a class="read-more">READ MORE</a>
  </article>
</section>

<div class="h-rule" style="top:2708px"></div>

<section class="partners">
  <h2 class="section-title center-title" style="top:2770px">OUR PARTNERS</h2>
  <div class="partner" style="left:98px">Calderon</div>
  <div class="partner" style="left:353px">Westmark Aerial</div>
  <div class="partner" style="left:610px">Tarrow Vance Ellery</div>
  <div class="partner" style="left:865px">Meridian Systems</div>
</section>

<footer class="footer">
  <svg class="footer-base" width="1200" height="482" viewBox="0 0 1200 482"><path d="M0 90 C180 40 330 20 520 60 C720 100 900 110 1200 10 L1200 482 L0 482 Z" fill="#28292b"/></svg>
  <div class="brand" style="left:100px;top:280px">
    <span class="brand-mark"></span>
    <span class="brand-name">Pellworth &amp; Quine<span class="brand-sub">A Health IT Company</span></span>
  </div>
  <div class="footer-col" style="left:455px">
    <h3>Information</h3>
    <ul class="footer-links"><li>Help</li><li>FAQ</li><li>Support</li><li>Sitemap</li><li>Terms Of Use</li><li>Privacy Statement</li></ul>
  </div>
  <div class="footer-col" style="left:623px">
    <h3>Newsletter Subscription</h3>
    <p style="margin-top:22px">Register your Email Address to get<br>information about us</p>
    <div class="email-field">Email Address</div>
    <div class="subscribe">SUBSCRIBE</div>
  </div>
  <div class="footer-col" style="left:933px">
    <h3>Contact Us</h3>
    <div style="margin-top:22px">
      <div class="contact-row"><svg width="12" height="16" viewBox="0 0 12 16"><path d="M6 0a6 6 0 0 1 6 6c0 4-6 10-6 10S0 10 0 6a6 6 0 0 1 6-6z" fill="#fff"/><circle cx="6" cy="6" r="2.2" fill="#28292b"/></svg>Level 2, 17 Harbor<br>Street, Lakeview 0412</div>
      <div class="contact-row"><svg width="14" height="14" viewBox="0 0 14 14"><path d="M3 0l3 3-2 2a8 8 0 0 0 5 5l2-2 3 3-2 3C6 14 0 8 0 3z" fill="#fff"/></svg>1 555 010 0199</div>
      <div class="contact-row"><svg width="15" height="12" viewBox="0 0 15 12"><rect width="15" height="12" fill="#fff"/><path d="M0 0l7.5 6L15 0" fill="none" stroke="#28292b" stroke-width="1.5"/></svg>info@pellworthquine.com</div>
    </div>
  </div>
  <div class="footer-rule"></div>
  <p class="copyright">Copyrights © 2018, Pellworth &amp; Quine. All rights reserved.</p>
  <div class="socials" aria-label="Social media links"><span></span><span></span><span></span></div>
</footer>

</body>
</html>
```